Counseling Practice Business Card

I need a professional looking business card incorporating my new logo that was just completed. Card needs to incorporate my name and title, description of my specialty, my address, my phone number, my fax number, my email and my website URL. I need to be able to choose design on/with different paper colors and textures.
I do not have a lot of business card ideas so I am open to anything but I want bold,sharp, clear card without additional designs other than my logo (see attached file info). I am open to different color backgrounds or paper colors including black. I do not like traditional brackets around area codes in phone number or dashes between numbers in phone number. Am open to other ways of presenting including periods between numbers as appropriate. I do not know enough to know what I like yet but I want card to coordinate and work together with my logo. My practice emphasizes natural mental health interventions so any use of color (with background paper color or the blue and green in my logo) that elicits nature is nice. In addition to black, any natural brown or wood looking background might be desirable also. Most of the offerings so far look very similar and boring.

Target Market(s)

Potential therapy clients and other professionals

Contact Information for Business Card

Card information:
Gerald M. Whitcombe, Ph.D.
Licensed Clinical Psychologist
Integrative Health Coach
4812 Marlowe Ridge Blvd SE
Suite 310
Duluth, GA 30096
770.415.2983 phone
770.581.4096 fax
drgeraldwhitcombe@quillmarsh.net
brightfernwellness.net

Font styles to use
Serif
Sans Serif
Other font styles liked:
• anything that you think looks crisp, clear and easily readable

Requirements
Must have
• Any color used should coordinate with my logo design (see attached files).
• Card should be printed horizontally so top and bottom are longest sides of rectangle.
• Background color or paper color should complement and highlight logo. Do not like a white background. black, grey, brown or any color my logo would blend well with.
Nice to have
• I would like designer to utilize color to highlight letters/name or phone-fax-web symbols.
• Bottom edge of card could be highlighted if appropriate to an idea.
Should not have
• I would NOT want the card to have a pure white background at all.
• No clear cards.
• Cards should be oriented with long sides on bottom and top, NOT sides. DO NOT LIKE THIS THIN TALL ORIENTATION.

```html
<!DOCTYPE html>
<html lang="en">
<head>
<meta charset="utf-8">
<title>Brightfern Wellness – Business Card</title>
<link rel="stylesheet" href="https://fonts.googleapis.com/css2?family=Roboto:wght@400;500;700&display=swap">
<style>
  :root {
    --backdrop: #1b1b1d;
    --card: #141415;
    --card-edge: #232325;
    --brand-front: #b9b9bb;
    --brand-back: #3a3a3d;
    --text-strong: #e4e4e6;
    --text-body: #c9c9cc;
    --fern: #7fae6a;
    --moss: #5d8a4c;
  }
  * { box-sizing: border-box; margin: 0; padding: 0; }
  html, body {
    width: 1200px; height: 900px; overflow: hidden;
    background: var(--backdrop);
    font-family: "Roboto", Arial, sans-serif;
  }
  .canvas { position: relative; width: 1200px; height: 900px; }
  .card {
    position: absolute; left: 280px; width: 640px; height: 366px;
    background: var(--card);
    border: 1px solid var(--card-edge);
  }
  .card--front { top: 60px; }
  .card--back { top: 474px; }

  .brand {
    display: flex; align-items: center; gap: 14px;
    font-weight: 500; letter-spacing: 0.5px; white-space: nowrap;
  }
  .brand__dot { width: 14px; height: 14px; border-radius: 50%; background: var(--moss); }
  .card--front .brand {
    position: absolute; left: 0; right: 0; top: 150px;
    justify-content: center; font-size: 44px; color: var(--brand-front);
  }
  .card--back .brand {
    position: absolute; left: 34px; top: 146px;
    font-size: 27px; color: var(--brand-back);
  }
  .card--back .brand__dot { width: 10px; height: 10px; }

  .divider {
    position: absolute; left: 318px; top: 36px; width: 1px; height: 278px;
    background: var(--moss);
  }
  .contact { position: absolute; left: 338px; top: 34px; width: 290px; color: var(--text-body); }
  .contact__name { font-size: 22px; font-weight: 700; color: var(--text-strong); white-space: nowrap; }
  .contact__title { font-size: 16px; line-height: 1.4; margin-top: 4px; color: var(--fern); }
  .contact__address { font-size: 16px; line-height: 1.4; margin-top: 14px; }
  .contact__list { list-style: none; margin-top: 14px; font-size: 15.5px; }
  .contact__list li { display: flex; align-items: center; gap: 9px; line-height: 1.55; white-space: nowrap; }
  .contact__list svg { width: 12px; height: 12px; fill: var(--fern); flex: none; }
</style>
</head>
<body>
<main class="canvas">
  <section class="card card--front" aria-label="Card front">
    <div class="brand"><span class="brand__dot"></span>Brightfern Wellness</div>
  </section>

  <section class="card card--back" aria-label="Card back">
    <div class="brand"><span class="brand__dot"></span>Brightfern Wellness</div>
    <div class="divider"></div>
    <div class="contact">
      <p class="contact__name">Gerald M. Whitcombe, Ph.D.</p>
      <p class="contact__title">Licensed Clinical Psychologist<br>Integrative Health Coach</p>
      <p class="contact__address">4812 Marlowe Ridge Blvd SE<br>Suite 310 Duluth, GA 30096</p>
      <ul class="contact__list">
        <li><svg viewBox="0 0 24 24"><path d="M6.6 10.8a15.1 15.1 0 0 0 6.6 6.6l2.2-2.2c.3-.3.7-.4 1-.2 1.1.4 2.3.6 3.6.6.6 0 1 .4 1 1V20c0 .6-.4 1-1 1A17 17 0 0 1 3 4c0-.6.4-1 1-1h3.5c.6 0 1 .4 1 1 0 1.3.2 2.5.6 3.6.1.3 0 .7-.2 1z"/></svg>770.415.2983</li>
        <li><svg viewBox="0 0 24 24"><path d="M6 2h12v6H6zM3 9h18v9h-3v4H6v-4H3zm5 6v5h8v-5z"/></svg>770.581.4096</li>
        <li><svg viewBox="0 0 24 24"><path d="M2 5h20v14H2zm2 2v.5l8 5 8-5V7zm0 2.8V17h16V9.8l-8 5z"/></svg>drgeraldwhitcombe@quillmarsh.net</li>
        <li><svg viewBox="0 0 24 24"><path d="M12 2a10 10 0 1 0 0 20 10 10 0 0 0 0-20zm6.9 9h-3a15 15 0 0 0-1.2-5.6A8 8 0 0 1 18.9 11zM12 4c.9 1.2 1.8 3.7 1.9 7h-3.8c.1-3.3 1-5.8 1.9-7zM9.3 5.4A15 15 0 0 0 8.1 11h-3a8 8 0 0 1 4.2-5.6zM5.1 13h3a15 15 0 0 0 1.2 5.6A8 8 0 0 1 5.1 13zm6.9 7c-.9-1.2-1.8-3.7-1.9-7h3.8c-.1 3.3-1 5.8-1.9 7zm2.7-1.4a15 15 0 0 0 1.2-5.6h3a8 8 0 0 1-4.2 5.6z"/></svg>www.brightfernwellness.net</li>
      </ul>
    </div>
  </section>
</main>
</body>
</html>
```